Design a calming beauty medical salon & spa website based in Hong Kong

We need help building an informational website for a beauty salon in Hong Kong. The local salon provides facials, massages, body and other slimming treatments in a relaxing environment. We offer some non-invasive medical treatments, such as botox. Having built the business on word of mouth, it is now time for us to launch a website to help market the business better. Website requirements:

-Must be responsive
-Use vibrant but clean colours. not too many, 1-2 colours
-Must be bilingual (switch between Chinese traditional and English)
-Our current website is host on a server, not using any particular platforms like wordpress

Pages:
1/ Homepage
2/ About us (incorporate gallery of salon photos and history of company)
3/ Promotions and latest deals (and leads them to sign up for more info, maybe pop-up small window when you click on a promotion)
4/ Treatment menus
4.1/Body treatments
4.2/ Face treatments
4.3/ Slimming treatments
5/ Showcasing products sold (no e-commerce functionality, just showing off products)
6/ Contact us (tel, address, map, opening hrs)

Footer - must haves include contact us info, privacy policy, terms & conditions, copyright blurb, join our company/employment page (with a form)

For information (comparable websites we like):
http://veltora.com/
http://pambrix.com.hk/tc/aboutpambrix/background.php#centerenvi
Attaching a very first draft concept for this website
Attaching pictures of the beauty salon
Attaching logo

Target Market(s)

Hong Kong based, Chinese, females, 30-50+ age. 90% female clients.

Industry/Entity Type

Beauty Salon

Number of Pages Required

5+ page

Font styles to use
Sans Serif

Colors
f9d9e8
fbd3d4
fee3d5
fbe7d2
fee18a
fbf289
ffffff

Requirements
Must have
• interactive elements on website, such as scrolling banner photo headers
• incorporate photos of website salon
• connect to facebook page

```html
<!DOCTYPE html>
<html lang="en">
<head>
<meta charset="utf-8">
<title>Serenelle Beauty</title>
<link href="https://fonts.googleapis.com/css2?family=Lato:ital,wght@0,400;0,700;0,900;1,700&display=swap" rel="stylesheet">
<style>
:root{
  --purple:#5e2a7e;
  --ink:#3d3d3d;
  --text:#555;
  --grey:#777;
  --pink:#f9d9e8;
  --pink-deep:#f6c3cf;
  --rose:#fbd3d4;
  --peach:#fbe3d0;
  --nav:#fce8d8;
  --yellow:#fbf289;
  --ring:#fbf5bd;
  --label:#fee18a;
  --white:#fff;
}
*{margin:0;padding:0;box-sizing:border-box}
html,body{width:678px;height:1200px;overflow:hidden;background:var(--white)}
body{position:relative;font-family:"Lato",sans-serif;color:var(--text)}
.abs{position:absolute}
.brand{display:flex;align-items:center;gap:6px;color:var(--purple);font-weight:700;font-size:15px;white-space:nowrap}
.brand-dot{width:20px;height:20px;border-radius:50%;border:2px solid var(--purple)}
.social{width:18px;height:18px;border-radius:50%;background:#8a8a8a}
.phone{display:flex;align-items:center;gap:5px;color:var(--purple);font-weight:700;font-size:10px}
.phone svg{width:9px;height:9px;fill:var(--purple)}
.lang{font-size:7px;color:#d9a86c}
.lang span{color:#e9c9b0}
.nav{top:61px;left:0;width:678px;height:35px;background:var(--nav)}
.nav-item{position:absolute;top:0;height:35px;line-height:35px;font-size:8px;font-weight:700;color:#333;letter-spacing:.2px}
.nav-home{top:7px;height:21px;line-height:19px;padding:0 11px;border-radius:11px;background:var(--pink);border:1px solid var(--white);box-shadow:0 0 0 1px #f4c7d6}
.hero{top:96px;left:0;width:678px;height:290px}
.hero-photo{position:absolute;left:80px;top:0;width:270px;height:270px;background:radial-gradient(ellipse at 45% 45%,#f3ddd3 0%,#f6e2df 45%,rgba(251,217,224,0) 75%)}
.hero-brand{left:400px;top:178px;font-size:22px}
.hero-brand .brand-dot{width:28px;height:28px;border-width:3px}
.tagline{left:382px;top:238px;font-size:18px;font-weight:700;font-style:italic;color:#444}
.section-title{left:0;width:678px;text-align:center;color:var(--ink);font-size:16px;font-weight:700;letter-spacing:.3px}
.rule{left:319px;width:40px;height:2px;background:var(--pink-deep)}
.intro{top:456px;left:0;width:678px;text-align:center;font-size:9.2px;line-height:17.5px;color:#444}
.intro strong{display:block;margin-top:5px}
.service{width:170px;height:170px;border-radius:50%;background:var(--ring);top:551px}
.service-photo{position:absolute;left:10px;top:10px;width:150px;height:150px;border-radius:50%;overflow:hidden}
.service-label{position:absolute;left:0;bottom:0;width:150px;height:40px;background:rgba(70,45,35,.72);color:var(--label);font-size:11px;font-weight:700;text-align:center;line-height:32px;letter-spacing:.3px}
.contact{top:757px;left:0;width:678px;height:285px;background:var(--peach)}
.label{font-size:10px;font-weight:700;color:#333}
.line{font-size:8.4px;color:#444;line-height:12px;display:flex;gap:8px}
.line svg{width:8px;height:8px;fill:#444;flex:none;margin-top:2px}
.line b{font-weight:700;color:#333}
.hours{font-size:8.4px;color:#444;display:flex}
.hours span:first-child{width:94px}
.map{left:306px;top:837px;width:296px;height:177px;border:5px solid var(--yellow);background:linear-gradient(160deg,#fdf2ea 0%,#fbeee4 60%,#f0efef 100%)}
.foot-col{font-size:7.6px;color:#444;line-height:12px}
.foot-head{font-size:8.4px;font-weight:700;color:#333;margin-bottom:6px;letter-spacing:.2px}
.email-input{left:368px;top:1096px;width:126px;height:22px;border:1px solid #bbb;border-radius:11px;font-size:7px;color:#555;line-height:20px;padding-left:10px}
.join-btn{left:442px;top:1124px;width:52px;height:20px;border-radius:10px;background:var(--pink);color:#444;font-size:7.4px;font-weight:700;text-align:center;line-height:20px}
</style>
</head>
<body>

<header>
  <div class="abs brand" style="left:42px;top:20px"><span class="brand-dot"></span>Serenelle Beauty</div>
  <span class="abs social" style="left:367px;top:21px"></span>
  <span class="abs social" style="left:396px;top:21px"></span>
  <div class="abs phone" style="left:434px;top:24px"><svg viewBox="0 0 24 24"><path d="M6.6 10.8a15 15 0 0 0 6.6 6.6l2.2-2.2c.3-.3.7-.4 1-.2 1.1.4 2.3.6 3.6.6.6 0 1 .4 1 1V20c0 .6-.4 1-1 1A17 17 0 0 1 3 4c0-.6.4-1 1-1h3.5c.6 0 1 .4 1 1 0 1.3.2 2.5.6 3.6.1.3 0 .7-.2 1z"/></svg>2655 0147</div>
  <div class="abs phone" style="left:511px;top:24px"><svg viewBox="0 0 24 24"><rect x="6" y="1" width="12" height="22" rx="2"/><rect x="8" y="4" width="8" height="14" fill="#fff"/></svg>6380 2291</div>
  <div class="abs lang" style="left:600px;top:26px">中文 <span>|</span> <span>EN</span></div>
</header>

<nav class="abs nav">
  <span class="nav-item nav-home" style="left:67px">HOME</span>
  <span class="nav-item" style="left:133px">ABOUT US</span>
  <span class="nav-item" style="left:202px">PROMOTIONS &amp; LATEST DEALS</span>
  <span class="nav-item" style="left:352px">TREATMENT</span>
  <span class="nav-item" style="left:429px">PRODUCTS SHOWCASE</span>
  <span class="nav-item" style="left:549px">CONTACT US</span>
</nav>

<section class="abs hero">
  <svg class="abs" style="left:0;top:0" width="678" height="290" viewBox="0 0 678 290">
    <defs>
      <linearGradient id="heroBg" x1="0" y1="0" x2="1" y2="0">
        <stop offset="0" stop-color="#fbe9ec"/>
        <stop offset="0.5" stop-color="#fad9df"/>
        <stop offset="1" stop-color="#f9cfd6"/>
      </linearGradient>
    </defs>
    <path d="M0 0H678V258Q540 290 390 285Q180 276 0 256Z" fill="url(#heroBg)"/>
  </svg>
  <div class="hero-photo" role="img" aria-label="Portrait of a smiling woman with clear skin"></div>
  <div class="abs brand hero-brand" style="top:82px"><span class="brand-dot"></span>Serenelle Beauty</div>
  <div class="abs tagline" style="top:142px">Excellent Medical Beauty</div>
</section>

<section>
  <h2 class="abs section-title" style="top:412px">ALL FOR BEAUTY SERVICES</h2>
  <div class="abs rule" style="top:439px"></div>
  <p class="abs intro">To take care of all aspects of the skin different needs, providing facial and body care,<br>Customers can enjoy a more efficient and beautiful skin treatment in a relaxed and comfortable environment.<br>Together with noble Swiss brand Serenelle organic material series for home care,<strong>In order to push the quality of skin to the pinnacle.</strong></p>

  <div class="abs service" style="left:51px">
    <div class="service-photo" role="img" aria-label="Woman relaxing with a facial mask" style="background:linear-gradient(150deg,#e9e4e2,#cfc3c0 55%,#a99590)">
      <div class="service-label">FACIALS</div>
    </div>
  </div>
  <div class="abs service" style="left:253px">
    <div class="service-photo" role="img" aria-label="Hot stone body care treatment" style="background:linear-gradient(150deg,#e0a060,#a55b2a 55%,#4a2a1c)">
      <div class="service-label">BODY CARE</div>
    </div>
  </div>
  <div class="abs service" style="left:457px">
    <div class="service-photo" role="img" aria-label="Therapist giving a slimming massage" style="background:linear-gradient(150deg,#d8c6b8,#a07a5c 55%,#5b4b5e)">
      <div class="service-label">THIN SHAPE</div>
    </div>
  </div>
</section>

<section class="abs contact">
  <h2 class="abs section-title" style="top:26px">CONTACT US</h2>
  <div class="abs rule" style="top:54px"></div>
</section>
<div class="abs label" style="left:93px;top:850px">CONTACT ADDRESS</div>
<div class="abs line" style="left:93px;top:870px"><svg viewBox="0 0 24 24"><path d="M12 2a7 7 0 0 0-7 7c0 5 7 13 7 13s7-8 7-13a7 7 0 0 0-7-7zm0 9.5A2.5 2.5 0 1 1 12 6.5a2.5 2.5 0 0 1 0 5z"/></svg><span>21st Floor, Harbour Jade Centre,<br>12-14 Lantana Road Tsim Sha Tsui, Kowloon</span></div>
<div class="abs line" style="left:93px;top:900px"><svg viewBox="0 0 24 24"><path d="M6.6 10.8a15 15 0 0 0 6.6 6.6l2.2-2.2c.3-.3.7-.4 1-.2 1.1.4 2.3.6 3.6.6.6 0 1 .4 1 1V20c0 .6-.4 1-1 1A17 17 0 0 1 3 4c0-.6.4-1 1-1h3.5c.6 0 1 .4 1 1 0 1.3.2 2.5.6 3.6.1.3 0 .7-.2 1z"/></svg><b>Inquiry Hotline: 26550147,&nbsp;&nbsp; 6380229</b></div>
<div class="abs line" style="left:93px;top:917px"><svg viewBox="0 0 24 24"><path d="M2 5h20v14H2z"/><path d="M2 5l10 8 10-8" fill="none" stroke="#fbe3d0" stroke-width="2"/></svg><b>Email: hello@serenellebeauty.com.hk</b></div>
<div class="abs label" style="left:93px;top:953px">HOURS</div>
<div class="abs hours" style="left:93px;top:971px"><span>Monday to Friday:</span><span>10:30 am to 9:30 pm</span></div>
<div class="abs hours" style="left:93px;top:989px"><span>Saturday and holidays:</span><span>10:30 am to 7:30 pm</span></div>
<div class="abs map" role="img" aria-label="Street map showing the salon location in Tsim Sha Tsui">
  <svg class="abs" style="left:140px;top:62px" width="14" height="18" viewBox="0 0 24 32"><path d="M12 0a10 10 0 0 0-10 10c0 8 10 22 10 22s10-14 10-22A10 10 0 0 0 12 0z" fill="#e53935"/><circle cx="12" cy="10" r="4" fill="#a51d1d"/></svg>
</div>

<footer>
  <div class="abs brand" style="left:42px;top:1083px"><span class="brand-dot"></span>Serenelle Beauty</div>
  <div class="abs foot-col" style="left:42px;top:1120px">Copyright © 2018. Company Name<br>All Right Reserved &nbsp;|&nbsp; Privacy Policy<br>Terms &amp; Conditions</div>
  <div class="abs foot-col" style="left:194px;top:1074px"><div class="foot-head">CONTACT INFO</div>21st Floor, Harbour Jade Centre,<br>12-14 Lantana Road Tsim Sha Tsui,<br>Kowloon<div style="margin-top:4px">Inquiry Hotline: 26550147 ,&nbsp; 6380229</div><div style="margin-top:4px">Email: hello@serenellebeauty.com.hk</div></div>
  <div class="abs foot-head" style="left:368px;top:1074px">JOIN OUR COMPANY</div>
  <div class="abs email-input">Enter Email Address</div>
  <div class="abs join-btn">JOIN</div>
  <div class="abs foot-head" style="left:534px;top:1074px">FOLLOW US</div>
  <span class="abs social" style="left:534px;top:1097px"></span>
  <span class="abs social" style="left:563px;top:1097px"></span>
</footer>

</body>
</html>
```